Website Design for Wheels for Servicemen.org - Donated Cars to Disabled Vets

Need a Wordpress website. The coding now, esp. the CDONT coding is not supported by many hosting sites. Looking for a landing page to generate leads.

Logo Text

look at current one for ideas

Coding

Coded - Design and coding required

Number of Pages Required

1 page

Requirements
Must have
• look at current website at www.wheelsforservicemen.org
Nice to have
• look at this site: http://givevehicletoservicemen.org

```html
<!DOCTYPE html>
<html lang="en">
<head>
<meta charset="utf-8">
<title>Wheels for Servicemen – Donate Your Car</title>
<link rel="stylesheet" href="https://fonts.googleapis.com/css2?family=Montserrat:wght@400;500;600;700&family=Open+Sans:wght@400;600&display=swap">
<style>
  :root{
    --blue:#0a5ec0;
    --blue-deep:#0a4fa3;
    --navy:#053a8a;
    --red:#d40d0d;
    --red-dark:#b20a0a;
    --yellow:#e8c600;
    --orange:#ff6a00;
    --btn-orange:#ff8c00;
    --ink:#3a3a3a;
    --muted:#444;
    --grey:#ededed;
    --white:#fff;
  }
  *{box-sizing:border-box;margin:0;padding:0}
  html,body{width:1103px;height:1200px;overflow:hidden;background:var(--white)}
  body{position:relative;font-family:'Open Sans',Arial,sans-serif;color:var(--ink)}
  .abs{position:absolute}

  /* header */
  .top-band{left:0;top:0;width:1103px;height:73px;background:var(--blue)}
  .nav-band{left:0;top:73px;width:1103px;height:45px;background:var(--blue-deep)}
  .brand{left:160px;top:18px;display:flex;align-items:center;gap:8px;font-family:'Montserrat',sans-serif;font-weight:600;font-size:15px;color:var(--white)}
  .brand-mark{width:14px;height:14px;border-radius:50%;background:var(--white)}
  .tagline{left:380px;top:27px;font-family:'Montserrat',sans-serif;font-weight:500;font-size:11.5px;color:var(--white)}
  .main-nav{left:188px;top:73px;height:45px;display:flex;font-family:'Montserrat',sans-serif;font-weight:500;font-size:11.5px;color:var(--white)}
  .main-nav a{display:flex;align-items:center;padding:0 13px;color:inherit;text-decoration:none}
  .main-nav a.active{background:var(--blue)}

  /* hero */
  .hero{left:0;top:118px;width:1103px;height:407px;
    background:linear-gradient(90deg,#5d6a5a 0%,#7d7a70 25%,#9a8f86 45%,#6f6a72 70%,#5b6270 100%)}
  .hero-title{left:600px;top:434px;width:356px;text-align:center;font-family:'Montserrat',sans-serif;color:var(--white)}
  .hero-title h1{font-weight:500;font-size:26px;letter-spacing:.5px;line-height:1}
  .hero-title p{font-weight:500;font-size:14px;margin-top:6px}
  .dots{left:888px;top:501px;display:flex;gap:8px}
  .dots span{width:10px;height:10px;border-radius:50%;background:var(--red)}
  .dots span:first-child{background:var(--white)}

  /* donation form */
  .form-panel{left:689px;top:0;width:266px;height:396px;background:var(--red)}
  .form-head{position:absolute;left:0;top:0;width:266px;height:94px;background:var(--red-dark);
    clip-path:polygon(0 0,100% 0,100% 75%,50% 100%,0 75%);text-align:center;color:var(--white);font-family:'Montserrat',sans-serif}
  .form-head .call{font-size:11.5px;font-weight:500;margin-top:15px}
  .form-head .phone{font-size:22px;font-weight:700;margin-top:2px}
  .form-head .hours{font-size:8.5px;font-weight:600;margin-top:3px}
  .field{position:absolute;left:32px;width:201px;height:22px;background:var(--white);font-size:7.5px;color:#555;padding:7px 9px;font-family:'Montserrat',sans-serif}
  .field svg{position:absolute;right:7px;top:8px}
  .donate-btn{position:absolute;left:85px;top:354px;width:94px;height:27px;background:var(--btn-orange);color:var(--white);font-family:'Montserrat',sans-serif;font-size:10px;font-weight:500;display:flex;align-items:center;justify-content:center}

  /* steps */
  .steps{left:149px;top:525px;width:806px;height:75px;display:flex}
  .step{flex:1;display:flex;align-items:center;padding-left:50px;gap:42px;color:var(--white);font-family:'Montserrat',sans-serif;font-weight:700;font-size:16px}
  .step.call{background:var(--yellow)}
  .step.tow{background:var(--orange)}
  .step.tax{background:var(--red)}

  /* reasons */
  .section-title{left:0;top:632px;width:1103px;text-align:center;font-family:'Montserrat',sans-serif;font-weight:700;font-size:20px;color:var(--navy)}
  .reason{width:230px}
  .reason svg{position:absolute;left:-32px;top:1px}
  .reason h3{font-family:'Montserrat',sans-serif;font-weight:700;font-size:13px;color:var(--ink);line-height:1.25}
  .reason p{font-size:8.5px;color:var(--muted);line-height:1.3;margin-top:5px}
  .cta{left:433px;top:856px;width:523px;height:68px;background:linear-gradient(100deg,var(--navy) 0%,var(--navy) 45%,#0649a0 45%,#0a55b0 100%);
    display:flex;align-items:center;justify-content:center;color:var(--white);font-family:'Montserrat',sans-serif;font-weight:700;font-size:23px}

  /* trust band */
  .trust{left:0;top:984px;width:689px;height:130px;background:var(--grey)}
  .trust-title{left:178px;top:1038px;font-family:'Montserrat',sans-serif;font-weight:700;font-size:19px;color:var(--navy)}
  .badge-a{left:390px;top:1024px;width:140px;height:50px;border-radius:6px;background:#d7d7d7}
  .badge-b{left:580px;top:1016px;width:66px;height:66px;border-radius:50%;background:#9cc4de}
  .program{left:689px;top:984px;width:414px;height:130px;background:var(--red)}
  .program h2{position:absolute;left:32px;top:40px;font-family:'Montserrat',sans-serif;font-weight:700;font-size:20px;color:var(--white);line-height:1.25}
  .program .go{position:absolute;left:214px;top:42px;width:47px;height:42px;border-radius:4px;background:var(--btn-orange);display:flex;align-items:center;justify-content:center}

  /* footer */
  .social{left:169px;top:1133px;display:flex;gap:8px}
  .social span{width:21px;height:21px;background:#3b7fc4}
  .social span:nth-child(3){background:#8aa04a}
  .social span:nth-child(4){background:#7a5a3a}
  .foot-nav{left:544px;top:1136px;display:flex;gap:26px;font-family:'Montserrat',sans-serif;font-weight:500;font-size:11.5px;color:#222}
  .copyright{left:739px;top:1166px;font-size:7.5px;color:#333;font-family:'Montserrat',sans-serif}
</style>
</head>
<body>

<header>
  <div class="abs top-band"></div>
  <div class="abs nav-band"></div>
  <div class="abs brand"><span class="brand-mark"></span>Wheels for Servicemen</div>
  <div class="abs tagline">DONATE YOUR CAR TO A VET , MAKE A DIFFERENCE</div>
  <nav class="abs main-nav">
    <a class="active" href="#">HOME</a>
    <a href="#">HOW IT WORKS</a>
    <a href="#">WHY DONATE YOUR CAR TO US?</a>
    <a href="#">FAQ</a>
  </nav>
</header>

<section>
  <div class="abs hero" role="img" aria-label="Photo of a young veteran in a wheelchair on a busy street, with a blurred crowd behind"></div>
  <div class="abs hero-title">
    <h1>DONATE YOUR CAR</h1>
    <p>FULL TAX DEDUCTION - RUNNING OR NOT</p>
  </div>
  <div class="abs dots"><span></span><span></span><span></span></div>

  <form class="abs form-panel">
    <div class="form-head">
      <div class="call">CALL TODAY TO DONATE</div>
      <div class="phone">1-800-555-0142</div>
      <div class="hours">Live Operators Available 7 Days a Week</div>
    </div>
    <div class="field" style="top:110px">Name</div>
    <div class="field" style="top:140px">Email</div>
    <div class="field" style="top:170px">Phone Number</div>
    <div class="field" style="top:201px">Cell Phone</div>
    <div class="field" style="top:231px">Address</div>
    <div class="field" style="top:262px">City</div>
    <div class="field" style="top:292px">State<svg width="8" height="5" viewBox="0 0 8 5"><path d="M0 0h8L4 5z" fill="#222"/></svg></div>
    <div class="field" style="top:322px">Zipcode</div>
    <div class="donate-btn">DONATE NOW</div>
  </form>
</section>

<section class="abs steps">
  <div class="step call">
    <svg width="20" height="20" viewBox="0 0 24 24"><path fill="#fff" d="M6.6 10.8a15.1 15.1 0 0 0 6.6 6.6l2.2-2.2c.3-.3.7-.4 1-.2 1.1.4 2.3.6 3.6.6.6 0 1 .4 1 1V20c0 .6-.4 1-1 1C10.6 21 3 13.4 3 4c0-.6.4-1 1-1h3.5c.6 0 1 .4 1 1 0 1.3.2 2.5.6 3.6.1.3 0 .7-.2 1z"/></svg>
    CALL US
  </div>
  <div class="step tow">
    <svg width="22" height="24" viewBox="0 0 22 24"><path fill="none" stroke="#fff" stroke-width="1.8" stroke-linejoin="round" d="M6 12V4a1.5 1.5 0 0 1 3 0v6V2.5a1.5 1.5 0 0 1 3 0V10V3.5a1.5 1.5 0 0 1 3 0V11V6a1.5 1.5 0 0 1 3 0v8c0 5-3 8-7 8-3 0-5-2-7-5l-2-3a1.5 1.5 0 0 1 2.5-1.6z"/></svg>
    WE TOW IT
  </div>
  <div class="step tax">
    <svg width="24" height="22" viewBox="0 0 24 22"><path fill="none" stroke="#fff" stroke-width="2" d="M16 4H3v16h16v-8"/><path fill="#fff" d="M20 1l3 3-10 10-4 1 1-4z"/></svg>
    TAX WRITE OFF
  </div>
</section>

<section>
  <h2 class="abs section-title">WHY DONATE YOUR CAR TO US?</h2>

  <div class="abs reason" style="left:193px;top:691px">
    <svg width="16" height="13" viewBox="0 0 16 13"><path fill="#444" d="M10 0l6 5.5-6 5.5V7.5C5 7.5 2 9 0 13c.5-6 4-9.5 10-9.5z"/></svg>
    <h3>IRS 501(C)3 APPROVED</h3><p>Free 24/7 Pickup with No DMV Hassles.</p>
  </div>
  <div class="abs reason" style="left:466px;top:691px">
    <svg width="16" height="13" viewBox="0 0 16 13"><path fill="#444" d="M10 0l6 5.5-6 5.5V7.5C5 7.5 2 9 0 13c.5-6 4-9.5 10-9.5z"/></svg>
    <h3>FREE LOCAL TOWING TO YOU</h3><p>We will pick up your car donation, running or not, when it's most convenient, at home or work.</p>
  </div>
  <div class="abs reason" style="left:744px;top:691px">
    <svg width="16" height="13" viewBox="0 0 16 13"><path fill="#444" d="M10 0l6 5.5-6 5.5V7.5C5 7.5 2 9 0 13c.5-6 4-9.5 10-9.5z"/></svg>
    <h3>ALL CARS ACCEPTED</h3><p>We take your car regardless of its condition or registration status.</p>
  </div>

  <div class="abs reason" style="left:193px;top:775px">
    <svg width="16" height="13" viewBox="0 0 16 13"><path fill="#444" d="M10 0l6 5.5-6 5.5V7.5C5 7.5 2 9 0 13c.5-6 4-9.5 10-9.5z"/></svg>
    <h3>INCOME TAX DEDUCTION</h3><p>We issue you an IRS tax receipt &amp; offer the largest resale network to get you the highest tax write-off possible.</p>
  </div>
  <div class="abs reason" style="left:466px;top:775px">
    <svg width="16" height="13" viewBox="0 0 16 13"><path fill="#444" d="M10 0l6 5.5-6 5.5V7.5C5 7.5 2 9 0 13c.5-6 4-9.5 10-9.5z"/></svg>
    <h3>NO PAPERWORK HASSLES</h3><p>We take any car and handle everything: DMV, Smog and IRS paperwork.</p>
  </div>
  <div class="abs reason" style="left:744px;top:775px">
    <svg width="16" height="13" viewBox="0 0 16 13"><path fill="#444" d="M10 0l6 5.5-6 5.5V7.5C5 7.5 2 9 0 13c.5-6 4-9.5 10-9.5z"/></svg>
    <h3>CAR DONATIONS HELP FUND PROGRAMS</h3><p>And benefit National Servicemen Support Fund. An IRS 501(c)3 nonprofit organization.</p>
  </div>

  <div class="abs reason" style="left:193px;top:865px">
    <svg width="16" height="13" viewBox="0 0 16 13"><path fill="#444" d="M10 0l6 5.5-6 5.5V7.5C5 7.5 2 9 0 13c.5-6 4-9.5 10-9.5z"/></svg>
    <h3>SCHEDULE A FREE PICKUP</h3><p>Complete the form and a representative will call you to arrange a convenient time to pickup your car.</p>
  </div>

  <div class="abs cta">DONATE YOUR CAR TODAY!</div>
</section>

<section>
  <div class="abs trust"></div>
  <div class="abs trust-title">SAFE &amp; SECURE</div>
  <div class="abs badge-a" role="img" aria-label="Security certification badge"></div>
  <div class="abs badge-b" role="img" aria-label="Approved charity seal"></div>
  <div class="abs program">
    <h2>CAR DONATION<br>PROGRAM</h2>
    <div class="go"><svg width="14" height="20" viewBox="0 0 14 20"><path d="M3 2l8 8-8 8" fill="none" stroke="#fff" stroke-width="3.5"/></svg></div>
  </div>
</section>

<footer>
  <div class="abs social"><span></span><span></span><span></span><span></span></div>
  <nav class="abs foot-nav"><span>HOME</span><span>HOW IT WORKS</span><span>WHY DONATE YOUR CAR TO US?</span><span>FAQ</span></nav>
  <div class="abs copyright">© 2016 www.wheelsforservicemen.org &nbsp;|&nbsp; All Rights Reserved.</div>
</footer>

</body>
</html>
```